Design a New Business Card for Our Company

We are looking for fresh, unique, and a modern business card that reflects our roots as digital marketing agency focused on SEM.

Industry/Entity Type

Marketing

Contact Information for Business Card

looking for very unique out of the box designs. clean and modern that compliments our logo

Requirements
Must have
• colors should match our logo
• Front should have name, address, email, and phone/fax of the person, phone/fax are the same number
• back should have our url

```html
<!DOCTYPE html>
<html lang="en">
<head>
<meta charset="utf-8">
<title>Brightpath Media – Business Card</title>
<link href="https://fonts.googleapis.com/css2?family=Open+Sans:wght@400;600;700&display=swap" rel="stylesheet">
<style>
  :root {
    --backdrop: #3a3330;
    --card-dark: #111111;
    --brand-blue: #5b97d3;
    --text-light: #e6e6e6;
    --text-grey: #b9b9b9;
    --divider: #3c3c3c;
    --white: #ffffff;
  }
  * { margin: 0; padding: 0; box-sizing: border-box; }
  html, body { width: 1200px; height: 900px; overflow: hidden; }
  body {
    background: var(--backdrop);
    font-family: "Open Sans", Arial, sans-serif;
    position: relative;
  }
  .card {
    position: absolute;
    width: 525px;
    height: 300px;
    border-radius: 3px;
    overflow: hidden;
  }
  .card-front { left: 50px; top: 300px; background: var(--card-dark); }
  .card-back  { left: 625px; top: 300px; background: var(--brand-blue); }

  .brand {
    display: flex;
    align-items: center;
    gap: 14px;
  }
  .brand-dot {
    width: 40px; height: 40px; border-radius: 50%;
  }
  .brand-name {
    font-weight: 700;
    line-height: 1;
    letter-spacing: -0.5px;
  }

  .card-front .brand { position: absolute; left: 120px; top: 62px; }
  .card-front .brand-dot { background: var(--brand-blue); }
  .card-front .brand-name { color: var(--text-grey); font-size: 40px; }

  .holder {
    position: absolute;
    right: 280px;
    top: 176px;
    text-align: right;
    color: var(--text-light);
  }
  .holder-name { color: var(--brand-blue); font-size: 17px; font-weight: 600; line-height: 1.2; }
  .holder-role { font-size: 14px; margin-bottom: 10px; }
  .holder-address { font-size: 15px; line-height: 1.3; }

  .divider {
    position: absolute;
    left: 262px; top: 170px;
    width: 1px; height: 100px;
    background: var(--divider);
  }

  .contact-list {
    position: absolute;
    left: 280px; top: 168px;
    list-style: none;
    color: var(--text-light);
    font-size: 13.5px;
  }
  .contact-list li { display: flex; align-items: center; gap: 9px; height: 21px; }
  .contact-list svg { width: 12px; height: 12px; fill: var(--brand-blue); flex: none; }

  .card-back .brand { position: absolute; left: 50%; top: 112px; transform: translateX(-50%); }
  .card-back .brand-dot { background: var(--white); }
  .card-back .brand-name { color: var(--white); font-size: 44px; white-space: nowrap; }
  .back-url {
    position: absolute;
    left: 0; right: 0; top: 200px;
    text-align: center;
    color: var(--white);
    font-size: 14px;
  }
</style>
</head>
<body>

<section class="card card-front">
  <div class="brand">
    <span class="brand-dot"></span>
    <span class="brand-name">brightpath</span>
  </div>

  <div class="holder">
    <p class="holder-name">Daniel Reyes</p>
    <p class="holder-role">Managing Director</p>
    <p class="holder-address">48 Harbour Lane, Suite 5<br>Westport, 20417.</p>
  </div>

  <div class="divider"></div>

  <ul class="contact-list">
    <li>
      <svg viewBox="0 0 24 24" aria-hidden="true"><path d="M6.6 10.8a15.1 15.1 0 0 0 6.6 6.6l2.2-2.2c.3-.3.7-.4 1-.2 1.1.4 2.3.6 3.6.6.6 0 1 .4 1 1V20c0 .6-.4 1-1 1C10.6 21 3 13.4 3 4c0-.6.4-1 1-1h3.5c.6 0 1 .4 1 1 0 1.3.2 2.5.6 3.6.1.3 0 .7-.2 1z"/></svg>
      021-555 0148 372
    </li>
    <li>
      <svg viewBox="0 0 24 24" aria-hidden="true"><path d="M6 2h10l2 2v5H6zM4 10h16a2 2 0 0 1 2 2v6h-4v4H6v-4H2v-6a2 2 0 0 1 2-2zm4 7v3h8v-3z"/></svg>
      021-555 0148 372
    </li>
    <li>
      <svg viewBox="0 0 24 24" aria-hidden="true"><path d="M2 5h20v14H2zm2 2v.5l8 5 8-5V7z"/></svg>
      hello@brightpath.com
    </li>
    <li>
      <svg viewBox="0 0 24 24" aria-hidden="true"><circle cx="12" cy="12" r="10"/></svg>
      www.brightpath.com
    </li>
  </ul>
</section>

<section class="card card-back">
  <div class="brand">
    <span class="brand-dot"></span>
    <span class="brand-name">brightpath</span>
  </div>
  <p class="back-url">www.brightpath.com</p>
</section>

</body>
</html>
```